Pull Up Sign for Financial Services Business

Looking to design a pull-up retractable banner for events. A design which I could add a second banner to so something that could flow across more than one banner would be ideal.

I have included my logo and business card so you can get an idea of colours and our branding style.

A disability image will be required on the banner. Dimensions are in image attached.

Target Market(s)

QVAB (Disability) Participants

Industry/Entity Type

Disability/Finance

Other font styles liked:
• Raleway

Requirements
Must have
• Disability Image - match our branding. Text in image uploaded

```html
<!DOCTYPE html>
<html lang="en">
<head>
<meta charset="utf-8">
<title>Tandem Plan Care – Pull Up Banner</title>
<link href="https://fonts.googleapis.com/css2?family=Playfair+Display:wght@500;600&family=Poppins:wght@500;600;700&family=Allura&display=swap" rel="stylesheet">
<style>
  :root {
    --magenta: #a83267;
    --magenta-dark: #6e1c44;
    --teal: #0b7d76;
    --plum: #5a2a6b;
    --white: #ffffff;
    --stage: #ececec;
  }
  * { box-sizing: border-box; margin: 0; padding: 0; }
  html, body {
    width: 750px; height: 1200px; overflow: hidden;
    background: var(--stage);
  }
  .banner {
    position: absolute; left: 135px; top: 20px;
    width: 454px; height: 1096px;
    transform: scale(1.058); transform-origin: top left;
    background: var(--white);
    overflow: hidden;
    box-shadow: 0 10px 30px rgba(0,0,0,.18);
  }
  .banner-art { position: absolute; inset: 0; }
  .brand {
    position: absolute; top: 92px; left: 0; width: 100%;
    display: flex; justify-content: center; align-items: center; gap: 10px;
  }
  .brand-square { width: 30px; height: 30px; background: var(--magenta); }
  .brand-name {
    font-family: "Playfair Display", serif; font-weight: 600;
    font-size: 27px; color: var(--magenta); letter-spacing: 1px;
  }
  .headline {
    position: absolute; top: 186px; left: 0; width: 100%; text-align: center;
    font-family: "Playfair Display", serif; font-weight: 500;
    font-size: 68px; line-height: 1; color: var(--magenta); letter-spacing: 1px;
  }
  .tagline {
    position: absolute; top: 236px; left: 0; width: 100%; text-align: center;
    font-family: "Allura", cursive; font-size: 66px; line-height: 1;
    color: var(--teal); letter-spacing: 3px;
  }
  .features {
    position: absolute; top: 846px; left: 36px; width: 390px;
    display: flex; list-style: none;
    font-family: "Poppins", sans-serif; font-weight: 500;
    font-size: 12.5px; line-height: 15px; color: var(--white);
  }
  .features-col { list-style: none; padding-right: 8px; }
  .features-col + .features-col {
    border-left: 1px solid rgba(255,255,255,.45); padding-left: 10px; padding-right: 0;
  }
  .features-col li { position: relative; padding-left: 13px; margin-bottom: 2px; }
  .features-col li::before {
    content: ""; position: absolute; left: 0; top: 4px;
    width: 8px; height: 8px; border-radius: 50%; background: var(--teal);
  }
  .features-col li::after {
    content: ""; position: absolute; left: 2.3px; top: 5.5px;
    width: 2.5px; height: 4px; border: solid var(--white);
    border-width: 0 1.3px 1.3px 0; transform: rotate(40deg);
  }
  .phone {
    position: absolute; top: 950px; left: 34px;
    display: flex; align-items: center; gap: 6px;
    font-family: "Poppins", sans-serif; font-weight: 700;
    font-size: 58px; line-height: 1; color: var(--white); letter-spacing: -1px;
  }
  .phone-icon {
    width: 44px; height: 44px; border-radius: 50%;
    background: var(--magenta-dark);
    display: flex; align-items: center; justify-content: center;
  }
  .web {
    position: absolute; top: 1022px; left: 36px; width: 380px; height: 30px;
    border-radius: 8px; background: var(--teal);
    display: flex; align-items: center; justify-content: center;
    font-family: "Poppins", sans-serif; font-weight: 600;
    font-size: 15px; letter-spacing: 1.6px; color: var(--white);
  }
</style>
</head>
<body>
  <main class="banner">
    <svg class="banner-art" width="454" height="1096" viewBox="0 0 454 1096">
      <defs>
        <linearGradient id="photoTone" x1="0" y1="0" x2="1" y2="1">
          <stop offset="0" stop-color="#c49a6c"/>
          <stop offset=".45" stop-color="#8a6a55"/>
          <stop offset=".75" stop-color="#4d6a9a"/>
          <stop offset="1" stop-color="#2d3f6b"/>
        </linearGradient>
      </defs>
      <polygon class="magenta-field" points="0,612 454,700 454,1096 0,1096" fill="var(--magenta)"/>
      <rect class="frame-outline" x="90" y="330" width="90" height="90" rx="14"
            transform="rotate(45 135 375)" fill="none" stroke="#e6b8cc" stroke-width="1.2"/>
      <rect class="frame-outline" x="300" y="590" width="150" height="150" rx="16"
            transform="rotate(45 375 665)" fill="none" stroke="#e6b8cc" stroke-width="1.2"/>
      <polygon class="photo" role="img" aria-label="Photo of two smiling children hugging, one seated in a wheelchair"
               points="231,292 485,546 231,800 -23,546" fill="url(#photoTone)"/>
      <circle class="partner-badge" cx="231" cy="796" r="44" fill="var(--plum)" stroke="var(--magenta)" stroke-width="4"/>
    </svg>

    <div class="brand">
      <span class="brand-square"></span>
      <span class="brand-name">Tandem Plan Care</span>
    </div>

    <h1 class="headline">YOUR PLAN</h1>
    <p class="tagline">Your way</p>

    <div class="features">
      <ul class="features-col">
        <li>Invoices processed daily</li>
        <li>Providers paid within<br>3 business days</li>
        <li>Expense reimbursements</li>
        <li>Real time funding access</li>
      </ul>
      <ul class="features-col">
        <li>Your own personal dedicated<br>plan manager</li>
        <li>Monthly statements</li>
        <li>Choice and control<br>use both registered and<br>unregistered providers</li>
      </ul>
    </div>

    <div class="phone">
      <span class="phone-icon">
        <svg width="24" height="24" viewBox="0 0 24 24" aria-hidden="true">
          <path d="M6.6 10.8a15 15 0 0 0 6.6 6.6l2.2-2.2a1 1 0 0 1 1-.25 11.4 11.4 0 0 0 3.6.57 1 1 0 0 1 1 1V20a1 1 0 0 1-1 1A17 17 0 0 1 3 4a1 1 0 0 1 1-1h3.5a1 1 0 0 1 1 1c0 1.25.2 2.45.57 3.57a1 1 0 0 1-.25 1z" fill="var(--white)"/>
        </svg>
      </span>
      <span class="phone-number">1300 555 01</span>
    </div>

    <div class="web">www.tandemplancare.com.au</div>
  </main>
</body>
</html>
```